Defense contractor needs a roll-up for an exhibition

The booth we have booked has only a size of 3m².
So this will be the centerpiece of the whole booth.
We need a roll-up that attracts visitors and at the same time it should contain already designed graphics. These graphics are giving visitors an overview of our system. So it is necessary to have them exposed in a height that the booth personal can conveniently point with its fingers at them.
For information about our company and product visit:
https://www.brellowtrackline.com/
For designing you should use Adobe Illustrator and the templates provided in the zip file, to guarantee a perfect print.
I have supplied my business card that you can copy the logo. As the company logo will be already at the booth nearby the top of the roll-up, you should not place it there. It can be in the middle or at the bottom.
I have uploaded a picture of the booth. The roll up will be placed at the left of the screen and has a size of 80cm x 200cm

Defense

Defense

Serif

0054AA
0677BA
7BADD7
CADEEF
E8F1F8

• you must use the Adobe Illustrator template to have a good printing result
• company logo on the upper side of the roll-up

```html
<!DOCTYPE html>
<html lang="en">
<head>
<meta charset="utf-8">
<title>Brellow Trackline – Advanced Combat Training Systems Roll-up</title>
<link rel="stylesheet" href="https://fonts.googleapis.com/css2?family=Oswald:wght@700&family=Montserrat:wght@500;600;700&display=swap">
<style>
  :root {
    --page: #ffffff;
    --panel: #e8ecf8;
    --ink: #000000;
    --navy: #0a1a4a;
    --royal: #1e55d6;
    --bright: #2f6fe8;
    --sky: #58b8ff;
    --white: #ffffff;
  }
  html, body {
    margin: 0;
    padding: 0;
    width: 1200px;
    height: 2246px;
    overflow: hidden;
    background: var(--page);
  }
  .rollup {
    position: absolute;
    left: 160px;
    top: 25px;
    width: 880px;
    height: 2196px;
    box-shadow: 0 6px 18px rgba(0,0,0,0.25);
  }
  .rollup svg { display: block; width: 100%; height: 100%; }
  .display { font-family: "Oswald", "Arial Narrow", sans-serif; font-weight: 700; }
  .sans { font-family: "Montserrat", Arial, sans-serif; }
</style>
</head>
<body>
<main class="rollup">
  <svg viewBox="0 0 480 1198" xmlns="http://www.w3.org/2000/svg">
    <defs>
      <clipPath id="hero-shape">
        <polygon points="0,153 42,153 80,116 160,116 197,153 280,153 318,116 398,116 437,153 480,153 480,548 0,548"/>
      </clipPath>
      <linearGradient id="hero-sky" x1="0" y1="0" x2="0" y2="1">
        <stop offset="0" stop-color="#1a35b8"/>
        <stop offset="0.35" stop-color="#2448d4"/>
        <stop offset="0.6" stop-color="#4a4fb8"/>
        <stop offset="0.75" stop-color="#3a5ad0"/>
        <stop offset="1" stop-color="#1a2a70"/>
      </linearGradient>
      <radialGradient id="sunset-glow" cx="0.5" cy="0.5" r="0.5">
        <stop offset="0" stop-color="#f2a6a0" stop-opacity="0.95"/>
        <stop offset="0.45" stop-color="#c27aa8" stop-opacity="0.7"/>
        <stop offset="1" stop-color="#6a4aa8" stop-opacity="0"/>
      </radialGradient>
      <radialGradient id="violet-haze" cx="0.5" cy="0.5" r="0.5">
        <stop offset="0" stop-color="#9a7ad8" stop-opacity="0.8"/>
        <stop offset="1" stop-color="#9a7ad8" stop-opacity="0"/>
      </radialGradient>
      <radialGradient id="horizon-light" cx="0.5" cy="0.5" r="0.5">
        <stop offset="0" stop-color="#9ad8ff" stop-opacity="0.9"/>
        <stop offset="1" stop-color="#4a8ae8" stop-opacity="0"/>
      </radialGradient>
      <linearGradient id="ground-shade" x1="0" y1="0" x2="0" y2="1">
        <stop offset="0" stop-color="#000" stop-opacity="0"/>
        <stop offset="0.45" stop-color="#000" stop-opacity="0.85"/>
        <stop offset="1" stop-color="#000"/>
      </linearGradient>
      <radialGradient id="vehicle-shade" cx="0.5" cy="0.6" r="0.5">
        <stop offset="0" stop-color="#000" stop-opacity="0.95"/>
        <stop offset="0.7" stop-color="#000" stop-opacity="0.7"/>
        <stop offset="1" stop-color="#000" stop-opacity="0"/>
      </radialGradient>
      <linearGradient id="badge-fill" x1="0" y1="0" x2="0" y2="1">
        <stop offset="0" stop-color="#2a8cf0"/>
        <stop offset="1" stop-color="#1b56d4"/>
      </linearGradient>
      <radialGradient id="faint-deco" cx="0.5" cy="0.5" r="0.5">
        <stop offset="0" stop-color="#cfd5e6"/>
        <stop offset="1" stop-color="#cfd5e6" stop-opacity="0"/>
      </radialGradient>
      <radialGradient id="system-tone" cx="0.5" cy="0.5" r="0.6">
        <stop offset="0" stop-color="#b9c3dc"/>
        <stop offset="0.6" stop-color="#d2d9ec"/>
        <stop offset="1" stop-color="#e8ecf8"/>
      </radialGradient>
    </defs>

    <!-- panel -->
    <rect class="panel" width="480" height="1198" fill="var(--panel)"/>
    <rect class="header-band" y="8" width="480" height="40" fill="#e2e7f5"/>
    <rect class="top-rail" width="480" height="8" fill="var(--ink)"/>

    <!-- company name -->
    <text class="display brand-name" x="240" y="72" text-anchor="middle" font-size="27" fill="var(--ink)" letter-spacing="0.5">BRELLOW TRACKLINE</text>

    <!-- hero -->
    <g class="hero" role="img" aria-label="Tank silhouette against a dramatic sunset sky with grass in the foreground" clip-path="url(#hero-shape)">
      <rect width="480" height="560" fill="url(#hero-sky)"/>
      <ellipse cx="130" cy="150" rx="90" ry="120" fill="url(#violet-haze)"/>
      <ellipse cx="120" cy="400" rx="200" ry="70" fill="url(#sunset-glow)"/>
      <ellipse cx="380" cy="360" rx="140" ry="50" fill="url(#sunset-glow)" opacity="0.6"/>
      <ellipse cx="200" cy="470" rx="200" ry="40" fill="url(#horizon-light)"/>
      <ellipse cx="270" cy="440" rx="220" ry="70" fill="url(#vehicle-shade)"/>
      <rect y="440" width="480" height="120" fill="url(#ground-shade)"/>
    </g>
    <text class="display hero-title" x="240" y="240" text-anchor="middle" font-size="50" fill="var(--white)" letter-spacing="-0.5">ADVANCED COMBAT</text>
    <text class="display hero-title" x="240" y="292" text-anchor="middle" font-size="50" fill="var(--white)" letter-spacing="-0.5">TRAINING SYSTEMS</text>
    <text class="sans hero-sub" x="238" y="315" text-anchor="middle" font-size="17.5" font-weight="700" fill="#e6ecff" letter-spacing="0.4">FOR REALISTIC COMBAT SIMULATION</text>

    <!-- services badge -->
    <rect class="hero-edge" x="0" y="547" width="480" height="2" fill="var(--sky)"/>
    <polygon class="badge-wing" points="95,548 120,513 360,513 420,548 375,583 115,583" fill="var(--navy)"/>
    <polygon class="badge" points="104,548 126,514 374,514 396,548 374,582 126,582" fill="url(#badge-fill)" stroke="var(--sky)" stroke-width="2"/>
    <text class="sans badge-label" x="248" y="564" text-anchor="middle" font-size="44" font-weight="700" fill="var(--white)" letter-spacing="1">SERVICES</text>

    <!-- faint vehicle decorations -->
    <ellipse class="deco" role="img" aria-label="Faint tank outline" cx="40" cy="620" rx="95" ry="32" fill="url(#faint-deco)"/>
    <ellipse class="deco" role="img" aria-label="Faint helicopter outline" cx="420" cy="690" rx="110" ry="36" fill="url(#faint-deco)"/>

    <!-- service list -->
    <g class="service">
      <polygon points="109,621 390,621 398,645 109,645" fill="var(--royal)"/>
      <rect x="72" y="614" width="37" height="37" fill="var(--ink)"/>
      <path d="M90.5 622 l8 3 v6 c0 5 -4 8 -8 10 c-4 -2 -8 -5 -8 -10 v-6z" fill="none" stroke="#fff" stroke-width="2"/>
      <text class="sans" x="131" y="639" font-size="17" font-weight="500" fill="var(--white)">Extended Warranty Programs</text>
    </g>
    <g class="service">
      <polygon points="109,670 297,670 305,694 109,694" fill="var(--royal)"/>
      <rect x="72" y="663" width="37" height="37" fill="var(--ink)"/>
      <path d="M81 672 l19 19 M100 672 l-19 19" stroke="#fff" stroke-width="3"/>
      <text class="sans" x="133" y="688" font-size="17" font-weight="500" fill="var(--white)">Logistics Support</text>
    </g>
    <g class="service">
      <polygon points="109,715 333,715 343,739 109,739" fill="var(--royal)"/>
      <rect x="72" y="708" width="37" height="37" fill="var(--ink)"/>
      <circle cx="90.5" cy="726.5" r="9" fill="none" stroke="#fff" stroke-width="3" stroke-dasharray="3 2"/>
      <circle cx="90.5" cy="726.5" r="4" fill="none" stroke="#fff" stroke-width="2"/>
      <text class="sans" x="133" y="733" font-size="17" font-weight="500" fill="var(--white)">Maintenance Contracts</text>
    </g>
    <g class="service">
      <polygon points="91,765 420,765 450,837 91,837" fill="var(--royal)"/>
      <rect x="72" y="760" width="37" height="37" fill="var(--ink)"/>
      <rect x="82" y="776" width="17" height="13" fill="none" stroke="#fff" stroke-width="2"/>
      <path d="M82 782 h17 M90.5 770 v6" stroke="#fff" stroke-width="2"/>
      <text class="sans" x="133" y="787" font-size="16.5" font-weight="500" fill="var(--white)">Long-term spare part services</text>
      <text class="sans" x="133" y="806" font-size="16.5" font-weight="500" fill="var(--white)">to keep the equipment in perfect</text>
      <text class="sans" x="133" y="825" font-size="16.5" font-weight="500" fill="var(--white)">operational condition</text>
    </g>

    <!-- tagline -->
    <polygon class="tag-frame" points="40,893 78,868 402,868 440,893 402,918 78,918" fill="none" stroke="var(--royal)" stroke-width="1" stroke-dasharray="2 2"/>
    <polygon class="tag-arrow" points="0,874 22,874 40,893 22,912 0,912" fill="var(--royal)"/>
    <polygon class="tag-arrow" points="480,874 458,874 440,893 458,912 480,912" fill="var(--royal)"/>
    <text class="sans tagline" x="240" y="889" text-anchor="middle" font-size="15" font-weight="700" fill="var(--ink)">EQUIP YOUR FIGHTING FORCE</text>
    <text class="sans tagline" x="240" y="907" text-anchor="middle" font-size="15" font-weight="700" fill="var(--ink)">WITH PRECISION TRAINING</text>

    <!-- system overview graphic -->
    <rect class="system-graphic" role="img" aria-label="Isometric overview of the training system: tanks, targets, a mobile control vehicle and a classroom simulator"
      x="0" y="935" width="480" height="210" fill="url(#system-tone)"/>

    <!-- footer -->
    <rect class="footer-line" x="0" y="1148" width="480" height="5" fill="var(--royal)"/>
    <rect class="footer" x="0" y="1153" width="480" height="45" fill="var(--ink)"/>
    <text class="sans footer-url" x="240" y="1183" text-anchor="middle" font-size="20" font-weight="600" fill="var(--white)" letter-spacing="0.3">www.brellowtrackline.com</text>
  </svg>
</main>
</body>
</html>
```